Just Sold Postcard

Real Estate/ Brindle Oak Realty.I'd like a template that I can use to change out the picture of the home, verbiage on the front, and address. I'm including a picture of what I've used in the past. I like designs that use red, with some blue and white. I'd like the ability to change the verbiage on the back as well.

Industry/Entity Type

Real Estate

Font styles to use
Serif
Sans Serif

```html
<!DOCTYPE html>
<html lang="en">
<head>
<meta charset="utf-8">
<title>Just Sold Postcard – Brindle Oak Realty</title>
<link rel="stylesheet" href="https://fonts.googleapis.com/css2?family=Questrial&family=Didact+Gothic&display=swap">
<style>
  :root {
    --stage: #333333;
    --card: #ffffff;
    --brand-red: #ee2a24;
    --brand-blue: #2e2a7a;
    --label-bg: #f1f1f4;
    --text-light: #ffffff;
    --photo-sky: #d9dcdf;
    --photo-roof: #4a4c52;
    --photo-brick: #9a6a50;
    --photo-ground: #5b4a3e;
  }
  * { margin: 0; padding: 0; box-sizing: border-box; }
  html, body { width: 1200px; height: 1000px; overflow: hidden; }
  body {
    background: var(--stage);
    position: relative;
    font-family: "Questrial", "Didact Gothic", sans-serif;
    color: var(--text-light);
  }
  .postcard {
    position: absolute;
    width: 577px;
    height: 436px;
    background: var(--card);
    box-shadow: 0 2px 6px rgba(0,0,0,.45);
    overflow: hidden;
  }
  .postcard--back { left: 197px; top: 111px; }
  .postcard--front { left: 454px; top: 449px; }

  .brand-name {
    font-family: "Questrial", sans-serif;
    color: var(--brand-red);
    white-space: nowrap;
    display: flex;
    align-items: center;
    gap: 8px;
  }
  .brand-name__dot {
    width: 12px; height: 12px;
    background: var(--brand-blue);
    border-radius: 50%;
    flex: none;
  }

  /* back side */
  .back__brand { position: absolute; left: 41px; top: 50px; font-size: 31px; }
  .back__panel {
    position: absolute; left: 0; top: 111px;
    width: 279px; height: 246px;
    background: var(--brand-red);
    padding: 18px 25px 0 41px;
  }
  .back__intro {
    font-size: 12px; line-height: 15px; letter-spacing: .6px;
    text-align: justify;
  }
  .back__agent { font-size: 21px; letter-spacing: .8px; margin-top: 14px; }
  .back__offer { font-size: 12px; line-height: 15px; margin-top: 6px; letter-spacing: .3px; margin-left: -2px; }
  .back__cta { font-family: "Didact Gothic", sans-serif; font-weight: 700; font-size: 15px; margin-top: 8px; letter-spacing: .4px; text-shadow: 0 0 1px #fff; }
  .back__contact { font-size: 12px; line-height: 16px; margin-top: 8px; letter-spacing: .3px; }

  /* front side */
  .front__art { position: absolute; inset: 0; }
  .front__tag {
    position: absolute; left: 0; top: 130px;
    width: 209px; height: 58px;
    background: var(--brand-red);
    font-size: 25px; letter-spacing: 2px; font-weight: 700;
    display: flex; align-items: center; justify-content: center;
  }
  .front__label {
    position: absolute; right: 0; top: 131px;
    width: 211px; height: 59px;
    background: var(--label-bg);
    display: flex; align-items: center; justify-content: center;
  }
  .front__label .brand-name { font-size: 21px; }
  .front__agent {
    position: absolute; right: 388px; top: 354px;
    text-align: right;
  }
  .front__agent-name { font-size: 22px; letter-spacing: .8px; font-weight: 700; line-height: 26px; }
  .front__agent-phone { font-size: 13px; letter-spacing: .8px; }
  .front__copy {
    position: absolute; left: 214px; top: 351px; width: 336px;
    font-size: 12px; line-height: 15px; letter-spacing: .4px;
  }
</style>
</head>
<body>

  <section class="postcard postcard--back" aria-label="Postcard back">
    <div class="brand-name back__brand"><span class="brand-name__dot"></span>Brindle Oak Realty</div>
    <div class="back__panel">
      <p class="back__intro">Lorem ipsum dolor sit amet, consectetur adipiscing elit Duis sed eleifend ex. Donecsapien ante, fermentumnon velit at, convallis suscipit tortor.</p>
      <p class="back__agent">Dana Whitlock</p>
      <p class="back__offer">For a free Market Analysis of your home.</p>
      <p class="back__cta">Contact me today</p>
      <p class="back__contact">Call: (555)-014-2290<br>Email: whitlock.dana@example.com</p>
    </div>
  </section>

  <section class="postcard postcard--front" aria-label="Postcard front">
    <svg class="front__art" width="577" height="436" viewBox="0 0 577 436">
      <defs>
        <linearGradient id="homePhoto" x1="0" y1="0" x2="0" y2="1">
          <stop offset="0" stop-color="var(--photo-sky)"/>
          <stop offset="0.22" stop-color="#c9ccd0"/>
          <stop offset="0.3" stop-color="var(--photo-roof)"/>
          <stop offset="0.5" stop-color="var(--photo-brick)"/>
          <stop offset="0.9" stop-color="#7d5644"/>
          <stop offset="1" stop-color="var(--photo-ground)"/>
        </linearGradient>
      </defs>
      <rect role="img" aria-label="Photo of the sold home: red brick house with chimneys under a grey sky" x="0" y="0" width="577" height="340" fill="url(#homePhoto)"/>
      <path d="M0 286 Q250 345 577 304 L577 436 L0 436 Z" fill="var(--brand-blue)"/>
      <path d="M0 298 Q250 352 577 312 L577 436 L0 436 Z" fill="var(--brand-red)"/>
    </svg>
    <div class="front__tag">JUST SOLD!</div>
    <div class="front__label"><div class="brand-name"><span class="brand-name__dot"></span>Brindle Oak Realty</div></div>
    <div class="front__agent">
      <p class="front__agent-name">Dana Whitlock</p>
      <p class="front__agent-phone">555-014-2290</p>
    </div>
    <p class="front__copy">Lorem ipsum dolor sit amet, consectetur adipiscing elit Duis sed eleifend ex. Donecsapien ante, fermentum-non velit at, convallis suscipit tortor. Proin elementum orci magna. Nulla vestibulum vitae ante</p>
  </section>

</body>
</html>
```